NimbaVault Website Homepage Design

Please provide your idea of homepage for a hosting company. This project is for DESIGN only, no coding.

It must use/combine colors used in logo, clean, modern look.

Homepage must consist of at least 4 sections (example: testimonials, services, and so on. not necesarily all of them). We would like the navigation to be horizontal, but not mandatory.

You can include a preview of services page (optional, not a must).

Number of Pages Required

1 page

Font styles to use
Sans Serif

```html
<!DOCTYPE html>
<html lang="en">
<head>
<meta charset="utf-8">
<title>NimbaVault Homepage</title>
<link href="https://fonts.googleapis.com/css2?family=Montserrat:wght@300;400;500;600;700&display=swap" rel="stylesheet">
<style>
:root{
  --blue-deep:#0646bb;
  --blue-mid:#0580d6;
  --blue-bright:#0499dd;
  --accent:#0a84d6;
  --ink:#444;
  --muted:#6d6d6d;
  --paper:#fff;
  --haze:#efefef;
  --card-top:#0a78d8;
  --card-bottom:#0b98e0;
}
*{box-sizing:border-box;margin:0;padding:0}
html,body{width:1200px;height:1200px;overflow:hidden;background:var(--paper);font-family:'Montserrat',sans-serif}
.hero-bg{position:absolute}
.nav a{position:absolute;color:#fff;text-decoration:none;font-weight:300}
.brand{position:absolute;color:#fff;font-weight:700;display:flex;align-items:center;gap:8px;justify-content:center;letter-spacing:1px}
.brand i{display:block;background:#fff;border-radius:2px}
.headline{position:absolute;color:#fff;font-weight:600;text-align:center}
.lede{position:absolute;color:#fff;text-align:center;font-weight:400;line-height:1.25}
.from{position:absolute;color:#fff;font-weight:700;text-align:center}
.price{position:absolute;color:#fff;font-weight:300;text-align:center}
.btn-ghost{position:absolute;border:1px solid #fff;color:#fff;border-radius:20px;display:flex;align-items:center;justify-content:center;font-weight:500}
.plan{position:absolute;background:#fff;box-shadow:0 3px 6px rgba(0,0,0,.22);display:flex;flex-direction:column;align-items:center;color:var(--ink);font-weight:600;text-align:center;line-height:1.2}
.plan svg{color:var(--accent)}
.haze{position:absolute}
.tagline{position:absolute;color:var(--accent);font-weight:600;text-align:center;letter-spacing:1.5px;line-height:1.1}
.domain{position:absolute;border:1px solid #b9b9b9;color:#999;display:flex;align-items:center;padding-left:4px;background:#fff}
.search{position:absolute;background:var(--accent);color:#fff;font-weight:700;display:flex;align-items:center;justify-content:center}
.section-title{position:absolute;color:var(--accent);font-weight:600;letter-spacing:2px;text-align:center}
.section-lede{position:absolute;color:var(--muted);text-align:center;line-height:1.25}
.service{position:absolute;background:linear-gradient(160deg,var(--card-top),var(--card-bottom));color:#fff;display:flex;flex-direction:column;align-items:center;text-align:center}
.service h3{font-weight:600;letter-spacing:1px}
.service p{line-height:1.3;font-weight:400}
.service .cta{border:1px solid #fff;border-radius:20px;display:flex;align-items:center;justify-content:center;font-weight:500}
.svc-d{width:137px;height:156px;border-radius:19px}
.svc-d svg{width:34px;height:36px;margin-top:12px}
.svc-d h3{font-size:8.5px;margin-top:11px}
.svc-d p{font-size:6.2px;width:115px;margin-top:9px}
.svc-d .cta{width:84px;height:24px;font-size:8.5px;margin-top:9px}
.svc-m{width:110px;height:126px;border-radius:17px}
.svc-m svg{width:28px;height:30px;margin-top:9px}
.svc-m h3{font-size:7px;margin-top:8px}
.svc-m p{font-size:4.6px;width:94px;margin-top:8px}
.svc-m .cta{width:67px;height:18px;font-size:6.5px;margin-top:7px}
.hamburger{position:absolute;width:20px;display:flex;flex-direction:column;gap:4px}
.hamburger span{height:3px;background:#fff;display:block}
</style>
</head>
<body>

<svg width="0" height="0" style="position:absolute" aria-hidden="true">
  <defs>
    <linearGradient id="heroGrad" x1="0" x2="1" y1="0" y2="0">
      <stop offset="0" stop-color="#0646bb"/>
      <stop offset=".5" stop-color="#0499dd"/>
      <stop offset="1" stop-color="#0646bb"/>
    </linearGradient>
    <linearGradient id="heroFacet" x1="0" x2="1" y1="0" y2="0">
      <stop offset="0" stop-color="#0a5ccb"/>
      <stop offset=".5" stop-color="#05a0e2"/>
      <stop offset="1" stop-color="#0a62cf"/>
    </linearGradient>
    <symbol id="i-shield" viewBox="0 0 40 44"><path d="M20 2 L36 7 V20 C36 31 28 38 20 42 C12 38 4 31 4 20 V7 Z M20 7 L31 10.5 V20 C31 28 26 33 20 36.5 C14 33 9 28 9 20 V10.5 Z" fill="none" stroke="currentColor" stroke-width="1.8" stroke-linejoin="round"/></symbol>
    <symbol id="i-target" viewBox="0 0 44 44"><g fill="none" stroke="currentColor" stroke-width="1.8"><circle cx="20" cy="24" r="17"/><circle cx="20" cy="24" r="12"/><circle cx="20" cy="24" r="7"/><circle cx="20" cy="24" r="2.5"/><path d="M20 24 L38 6 M33 4 V11 H40"/></g></symbol>
    <symbol id="i-rocket" viewBox="0 0 44 44"><g fill="none" stroke="currentColor" stroke-width="1.8" stroke-linejoin="round"><path d="M38 5 C28 5 18 13 13 25 L19 31 C31 26 39 16 38 5 Z"/><circle cx="28" cy="16" r="3"/><path d="M14 22 L6 22 L11 15 L19 15 M22 30 L22 38 L29 33 L29 25 M13 31 L6 38"/></g></symbol>
    <symbol id="i-chart" viewBox="0 0 44 44"><g fill="none" stroke="currentColor" stroke-width="1.8"><rect x="4" y="28" width="6" height="12"/><rect x="13" y="22" width="6" height="18"/><rect x="22" y="16" width="6" height="24"/><rect x="31" y="10" width="6" height="30"/><path d="M4 20 L36 4 M30 3 H37 V9"/></g></symbol>
    <symbol id="i-bulb" viewBox="0 0 44 44"><g fill="none" stroke="currentColor" stroke-width="1.8" stroke-linecap="round"><path d="M22 11 C15 11 11 16 11 21 C11 26 16 28 17 33 H27 C28 28 33 26 33 21 C33 16 29 11 22 11 Z M17 36 H27 M18 39 H26 M20 42 H24"/><path d="M22 2 V6 M8 7 L11 10 M36 7 L33 10 M3 19 H7 M37 19 H41"/></g></symbol>
    <symbol id="i-safe" viewBox="0 0 44 44"><g fill="none" stroke="currentColor" stroke-width="1.8"><rect x="4" y="3" width="36" height="34" rx="2"/><rect x="8" y="7" width="28" height="26"/><circle cx="22" cy="20" r="7"/><circle cx="22" cy="20" r="3"/><path d="M10 37 V41 H15 V37 M29 37 V41 H34 V37 M36 14 V26"/></g></symbol>
    <symbol id="i-site" viewBox="0 0 60 60"><circle cx="30" cy="30" r="26" fill="none" stroke="currentColor" stroke-width="5"/></symbol>
    <symbol id="i-server" viewBox="0 0 60 60"><g fill="none" stroke="currentColor" stroke-width="2.6"><rect x="6" y="4" width="48" height="12" rx="2"/><rect x="6" y="20" width="48" height="12" rx="2"/><rect x="6" y="36" width="48" height="12" rx="2"/><path d="M12 10h4M20 10h4M28 10h20M12 26h4M20 26h4M28 26h20M12 42h4M20 42h4M28 42h20M30 48v6M4 54h22M34 54h22"/><circle cx="30" cy="54" r="3"/></g></symbol>
    <symbol id="i-cloud" viewBox="0 0 60 60"><g fill="none" stroke="currentColor" stroke-width="2.2" stroke-linecap="round"><path d="M12 34 C4 34 3 23 10 21 C10 13 19 10 23 15 C25 5 40 4 42 15 C51 14 55 22 51 28 C56 32 51 36 47 34 Z"/><path d="M20 34v6l-4 4v4M27 34v14M34 34v8l4 4M41 34v4"/><circle cx="16" cy="50" r="2"/><circle cx="27" cy="50" r="2"/><circle cx="39" cy="48" r="2"/><circle cx="41" cy="40" r="2"/></g></symbol>
  </defs>
</svg>

<!-- ===== Desktop ===== -->
<section class="desktop" aria-label="Desktop homepage">
  <svg class="haze" style="left:82px;top:432px" width="400" height="142" viewBox="0 0 400 142"><polygon points="0,0 400,0 0,140" fill="var(--haze)"/></svg>
  <svg class="hero-bg" style="left:82px;top:60px" width="596" height="373" viewBox="0 0 596 373" preserveAspectRatio="none">
    <rect width="596" height="373" fill="url(#heroGrad)"/>
    <polygon points="0,0 596,0 298,45" fill="url(#heroFacet)" opacity=".8"/>
    <polygon points="0,373 596,373 298,335" fill="url(#heroFacet)" opacity=".8"/>
  </svg>
  <nav class="nav" style="font-size:14px">
    <a style="left:117px;top:105px">Home</a>
    <a style="left:203px;top:105px">Services</a>
    <a style="left:289px;top:105px">Testimonials</a>
    <a style="left:404px;top:105px">About</a>
    <a style="left:489px;top:105px">Contact</a>
  </nav>
  <div class="brand" style="left:82px;width:596px;top:134px;font-size:31px"><i style="width:12px;height:12px"></i>NimbaVault</div>
  <h1 class="headline" style="left:82px;width:596px;top:196px;font-size:19px;letter-spacing:2.2px">POWERED LIGHT FAST HOSTING</h1>
  <p class="lede" style="left:238px;width:284px;top:226px;font-size:6px">Lorem ipsum dolor sit amet, consectetur adipiscing elit, sed do eiusmod tempor incididunt ut labore et dolore magna aliqua. Ut enim ad minim veniam, quis nostrud exercitation ullamco laboris nisi ut aliquip ex ea commodo consequat. Duis aute irure dolor in</p>
  <p class="from" style="left:82px;width:596px;top:259px;font-size:17px">Starting at only</p>
  <p class="price" style="left:82px;width:596px;top:284px;font-size:17px">$2.75/mo*</p>
  <div class="btn-ghost" style="left:341px;top:320px;width:83px;height:24px;font-size:10.5px">Get started</div>

  <div class="plan" style="left:209px;top:422px;width:92px;height:106px;font-size:11px"><svg width="44" height="44" style="margin-top:18px"><use href="#i-site"/></svg><span style="margin-top:12px">Inkleaf<br>Hosting</span></div>
  <div class="plan" style="left:335px;top:422px;width:91px;height:106px;font-size:11px"><svg width="40" height="40" style="margin-top:20px"><use href="#i-server"/></svg><span style="margin-top:14px">Shared<br>Hosting</span></div>
  <div class="plan" style="left:462px;top:422px;width:91px;height:106px;font-size:11px"><svg width="46" height="46" style="margin-top:16px"><use href="#i-cloud"/></svg><span style="margin-top:10px">Dedicated<br>Hosting</span></div>

  <h2 class="tagline" style="left:82px;width:596px;top:554px;font-size:20.5px">Get your website, email and business<br>online today!</h2>
  <div class="domain" style="left:209px;top:615px;width:272px;height:19px;font-size:8.5px">Find the perfect domain for your business ...</div>
  <div class="search" style="left:486px;top:615px;width:70px;height:18px;font-size:10.5px">Search</div>

  <h2 class="section-title" style="left:82px;width:596px;top:718px;font-size:19px">SERVICES</h2>
  <p class="section-lede" style="left:192px;width:376px;top:746px;font-size:6.2px">Lorem ipsum dolor sit amet, consectetur adipiscing elit, sed do eiusmod tempor incididunt ut labore et dolore magna aliqua. Ut enim ad minim veniam, quis nostrud exercitation ullamco laboris nisi ut aliquip ex ea commodo consequat. Duis aute irure dolor in reprehenderit in voluptate velit esse cillum dolore eu fugiat nulla pariatur. Excepteur sint occae-</p>

  <div class="service svc-d" style="left:156px;top:803px"><svg><use href="#i-shield"/></svg><h3>SERVICE #1</h3><p>Lorem ipsum dolor sit amet, consectetur adipiscing elit, sed do eiusmod tempor incididunt ut labore et dolore magna aliqua. Ut enim ad</p><div class="cta">Call to Action</div></div>
  <div class="service svc-d" style="left:312px;top:803px"><svg><use href="#i-target"/></svg><h3>SERVICE #2</h3><p>Lorem ipsum dolor sit amet, consectetur adipiscing elit, sed do eiusmod tempor incididunt ut labore et dolore magna aliqua. Ut enim ad</p><div class="cta">Call to Action</div></div>
  <div class="service svc-d" style="left:468px;top:803px"><svg><use href="#i-rocket"/></svg><h3>SERVICE #3</h3><p>Lorem ipsum dolor sit amet, consectetur adipiscing elit, sed do eiusmod tempor incididunt ut labore et dolore magna aliqua. Ut enim ad</p><div class="cta">Call to Action</div></div>
  <div class="service svc-d" style="left:157px;top:993px"><svg><use href="#i-chart"/></svg><h3>SERVICE #4</h3><p>Lorem ipsum dolor sit amet, consectetur adipiscing elit, sed do eiusmod tempor incididunt ut labore et dolore magna aliqua. Ut enim ad</p><div class="cta">Call to Action</div></div>
  <div class="service svc-d" style="left:312px;top:993px"><svg><use href="#i-bulb"/></svg><h3>SERVICE #5</h3><p>Lorem ipsum dolor sit amet, consectetur adipiscing elit, sed do eiusmod tempor incididunt ut labore et dolore magna aliqua. Ut enim ad</p><div class="cta">Call to Action</div></div>
  <div class="service svc-d" style="left:468px;top:993px"><svg><use href="#i-safe"/></svg><h3>SERVICE #6</h3><p>Lorem ipsum dolor sit amet, consectetur adipiscing elit, sed do eiusmod tempor incididunt ut labore et dolore magna aliqua. Ut enim ad</p><div class="cta">Call to Action</div></div>
</section>

<!-- ===== Mobile ===== -->
<section class="mobile" aria-label="Mobile homepage">
  <svg class="haze" style="left:830px;top:460px" width="160" height="78" viewBox="0 0 160 78"><polygon points="0,0 160,0 0,76" fill="var(--haze)"/></svg>
  <svg class="hero-bg" style="left:830px;top:54px" width="251" height="411" viewBox="0 0 251 411" preserveAspectRatio="none">
    <rect width="251" height="411" fill="url(#heroGrad)"/>
    <polygon points="0,0 251,0 125,40" fill="url(#heroFacet)" opacity=".8"/>
  </svg>
  <div class="hamburger" style="left:1042px;top:70px"><span></span><span></span><span></span></div>
  <div style="position:absolute;left:830px;top:104px;width:251px;height:20px;overflow:hidden">
    <span style="position:absolute;left:153px;top:1px;color:#fff;font-weight:300;font-size:14px">Support</span>
    <span style="position:absolute;left:239px;top:1px;color:#fff;font-weight:300;font-size:14px">Sign in</span>
  </div>
  <div class="brand" style="left:830px;width:251px;top:130px;font-size:25px;gap:6px"><i style="width:10px;height:10px"></i>NimbaVault</div>
  <h1 class="headline" style="left:830px;width:251px;top:183px;font-size:16.5px;letter-spacing:1.8px;line-height:1.15">POWERED LIGHT<br>FAST HOSTING</h1>
  <p class="lede" style="left:848px;width:216px;top:241px;font-size:5px">Lorem ipsum dolor sit amet, consectetur adipiscing elit, sed do eiusmod tempor incididunt ut labore et dolore magna aliqua. Ut enim ad minim veniam, quis nostrud exercitation ullamco laboris nisi ut aliquip ex ea commodo consequat. Duis aute irure dolor in reprehenderit in voluptate velit</p>
  <p class="from" style="left:830px;width:251px;top:290px;font-size:15px">Starting at only</p>
  <p class="price" style="left:830px;width:251px;top:314px;font-size:14px">$2.75/mo*</p>
  <div class="btn-ghost" style="left:917px;top:348px;width:78px;height:21px;font-size:9.5px">Get started</div>

  <div class="plan" style="left:837px;top:422px;width:74px;height:85px;font-size:8.5px"><svg width="36" height="36" style="margin-top:13px"><use href="#i-site"/></svg><span style="margin-top:11px">Inkleaf<br>Hosting</span></div>
  <div class="plan" style="left:919px;top:422px;width:73px;height:85px;font-size:8.5px"><svg width="30" height="30" style="margin-top:16px"><use href="#i-server"/></svg><span style="margin-top:14px">Shared<br>Hosting</span></div>
  <div class="plan" style="left:1002px;top:422px;width:73px;height:85px;font-size:8.5px;box-shadow:none;background:#fff"><svg width="34" height="34" style="margin-top:13px"><use href="#i-cloud"/></svg><span style="margin-top:13px">Dedicated<br>Hosting</span></div>

  <h2 class="tagline" style="left:830px;width:251px;top:528px;font-size:15.5px;line-height:1.15">Get your website, email<br>and business online<br>today!</h2>
  <div class="domain" style="left:846px;top:589px;width:219px;height:15px;font-size:6.5px">Find the perfect domain for your business ...</div>
  <div class="search" style="left:927px;top:616px;width:57px;height:13px;font-size:8px">Search</div>

  <h2 class="section-title" style="left:830px;width:251px;top:651px;font-size:15.5px">SERVICES</h2>
  <p class="section-lede" style="left:840px;width:231px;top:674px;font-size:4.8px">Lorem ipsum dolor sit amet, consectetur adipiscing elit, sed do eiusmod tempor incididunt ut labore et dolore magna aliqua. Ut enim ad minim veniam, quis nostrud exercitation ullamco laboris nisi ut aliquip ex ea commodo consequat. Duis aute irure dolor in reprehenderit in voluptate velit esse cillum dolore eu fugiat nulla pariatur. Excepteur sint occaecat cupidatat non proident, sunt in culpa qui officia deserunt mollit anim id est laborum</p>

  <div class="service svc-m" style="left:845px;top:744px"><svg><use href="#i-shield"/></svg><h3>SERVICE #1</h3><p>Lorem ipsum dolor sit amet, consectetur adipiscing elit, sed do eiusmod tempor incididunt ut labore et dolore magna aliqua. Ut enim ad</p><div class="cta">Call to Action</div></div>
  <div class="service svc-m" style="left:963px;top:744px"><svg><use href="#i-target"/></svg><h3>SERVICE #2</h3><p>Lorem ipsum dolor sit amet, consectetur adipiscing elit, sed do eiusmod tempor incididunt ut labore et dolore magna aliqua. Ut enim ad</p><div class="cta">Call to Action</div></div>
  <div class="service svc-m" style="left:846px;top:898px"><svg><use href="#i-chart"/></svg><h3>SERVICE #4</h3><p>Lorem ipsum dolor sit amet, consectetur adipiscing elit, sed do eiusmod tempor incididunt ut labore et dolore magna aliqua. Ut enim ad</p><div class="cta">Call to Action</div></div>
  <div class="service svc-m" style="left:963px;top:898px"><svg><use href="#i-bulb"/></svg><h3>SERVICE #5</h3><p>Lorem ipsum dolor sit amet, consectetur adipiscing elit, sed do eiusmod tempor incididunt ut labore et dolore magna aliqua. Ut enim ad</p><div class="cta">Call to Action</div></div>
  <div class="service svc-m" style="left:843px;top:1043px"><svg><use href="#i-rocket"/></svg><h3>SERVICE #3</h3><p>Lorem ipsum dolor sit amet, consectetur adipiscing elit, sed do eiusmod tempor incididunt ut labore et dolore magna aliqua. Ut enim ad</p><div class="cta">Call to Action</div></div>
  <div class="service svc-m" style="left:963px;top:1043px"><svg><use href="#i-safe"/></svg><h3>SERVICE #6</h3><p>Lorem ipsum dolor sit amet, consectetur adipiscing elit, sed do eiusmod tempor incididunt ut labore et dolore magna aliqua. Ut enim ad</p><div class="cta">Call to Action</div></div>
</section>

</body>
</html>
```